Banner ads for LP that work with same theme as below banners

Love the banner ads below. Need more with attached photos. But use the same wording, font as in below banner ads. Should be LP size 1200/627 so I can use for Pixorly and LP. Looking for great ads to use as LP ads. We do lots of ads so it will be worth your time to enter this contest you will be rewarded with a ton of work. Need several banner ads that work together. So maybe 1 of the dresses, 1 of the sweater, 1 of the leggings, 1 of the jacket

Target Market(s)

Women 24-45

Industry/Entity Type

Fashion

Requirements
Must have
• Banner ads that work for LP and Pixorly
Nice to have
• Several options to choose from
Should not have
• not sure

```html
<!DOCTYPE html>
<html lang="en">
<head>
<meta charset="UTF-8">
<title>Our Best Jacket Ever – Banner</title>
<link rel="stylesheet" href="https://fonts.googleapis.com/css2?family=Kaushan+Script&family=Playfair+Display:wght@400;700;900&display=swap">
<style>
  :root {
    --canvas-bg: #ffffff;
    --script-grey: #5f5f5f;
    --accent-blue: #1a6591;
    --button-grey: #6b6b6b;
    --button-text: #ffffff;
    --jacket-navy: #253f66;
    --knit-grey: #b9b9b9;
    --hair-tan: #b48c62;
  }
  * { margin: 0; padding: 0; box-sizing: border-box; }
  html, body {
    width: 1200px;
    height: 628px;
    overflow: hidden;
    background: var(--canvas-bg);
  }
  .banner {
    position: relative;
    width: 1200px;
    height: 628px;
    background: var(--canvas-bg);
    overflow: hidden;
  }
  .headline {
    position: absolute;
    left: 85px;
    top: 160px;
    width: 270px;
    text-align: center;
  }
  .headline__script {
    display: block;
    font-family: "Kaushan Script", cursive;
    color: var(--script-grey);
    font-size: 54px;
    line-height: 1;
    letter-spacing: 2px;
  }
  .headline__script--top { margin-left: 10px; }
  .headline__product {
    display: block;
    font-family: "Playfair Display", serif;
    font-weight: 900;
    color: var(--accent-blue);
    font-size: 46px;
    letter-spacing: 7px;
    line-height: 1;
    margin-top: 12px;
    margin-left: 22px;
  }
  .headline__script--bottom {
    margin-top: 18px;
    font-size: 58px;
    margin-left: 5px;
  }
  .cta {
    position: absolute;
    left: 85px;
    top: 376px;
    width: 269px;
    height: 61px;
    background: var(--button-grey);
    color: var(--button-text);
    font-family: "Playfair Display", serif;
    font-size: 19px;
    letter-spacing: 2.5px;
    display: flex;
    align-items: center;
    justify-content: center;
    text-decoration: none;
  }
  .cta__strong { font-weight: 900; }
  .cta__light { font-weight: 400; margin: 0 6px; }
  .model-photo {
    position: absolute;
    left: 822px;
    top: 0;
    width: 300px;
    height: 628px;
    background:
      linear-gradient(180deg,
        rgba(180,140,98,0.55) 0%,
        rgba(180,140,98,0.2) 28%,
        transparent 34%),
      linear-gradient(180deg,
        var(--canvas-bg) 0%,
        var(--jacket-navy) 32%,
        var(--jacket-navy) 72%,
        var(--knit-grey) 80%,
        #1c1c1c 88%,
        #1c1c1c 100%);
    border-radius: 120px 120px 0 0;
  }
</style>
</head>
<body>
  <main class="banner">
    <h1 class="headline">
      <span class="headline__script headline__script--top">Our Best</span>
      <span class="headline__product">JACKET</span>
      <span class="headline__script headline__script--bottom">Ever!</span>
    </h1>
    <a class="cta" href="#">
      <span class="cta__strong">SHOP</span><span class="cta__light">THE</span><span class="cta__strong">LOOK</span>
    </a>
    <div class="model-photo" role="img" aria-label="Photo of a woman wearing a navy quilted puffer jacket with a faux-fur collar and grey cable-knit hem, with black leggings"></div>
  </main>
</body>
</html>
```